HearthMile business card and stationary design

We are looking for a simple yet elegant design for our mortgage company business card and stationary.

The card should include:
Name (Marcus Pell)
Title (CEO)
Phone Number (732-555-0182)
Address (48 Birchwell Court, Suite 314, Larkmont, NJ 08150)
Email (email@hearthmile.example)
"NMLS" i.e. (NMLS 61947)
"Company NMLS" (Company NMLS 274615)

Contact Information for Business Card

See above

```html
<!DOCTYPE html>
<html lang="en">
<head>
<meta charset="utf-8">
<title>HearthMile business card</title>
<link rel="stylesheet" href="https://fonts.googleapis.com/css2?family=Montserrat:wght@400;500;600&display=swap">
<style>
  :root {
    --backdrop: #26272b;
    --card-navy: #1a2330;
    --accent-blue: #29a6e3;
    --text-white: #f4f6f8;
    --text-soft: #dfe5ea;
  }
  * { box-sizing: border-box; margin: 0; padding: 0; }
  html, body {
    width: 1200px;
    height: 786px;
    overflow: hidden;
    background: var(--backdrop);
    font-family: "Montserrat", Arial, sans-serif;
  }
  .canvas {
    width: 1200px;
    height: 786px;
    display: flex;
    align-items: center;
    justify-content: center;
    gap: 40px;
  }
  .card {
    position: relative;
    width: 540px;
    height: 309px;
    background: var(--card-navy);
    border: 7px solid var(--accent-blue);
    box-shadow: 0 18px 40px rgba(0, 0, 0, 0.45);
  }
  .brand-name {
    font-weight: 600;
    color: var(--text-white);
    letter-spacing: 0.5px;
    white-space: nowrap;
  }
  .card-front .brand-name {
    position: absolute;
    left: 34px;
    top: 168px;
    font-size: 34px;
  }
  .divider {
    position: absolute;
    left: 262px;
    top: 60px;
    width: 1px;
    height: 185px;
    background: var(--accent-blue);
  }
  .contact {
    position: absolute;
    left: 286px;
    top: 54px;
    color: var(--text-soft);
    font-size: 11.5px;
    line-height: 1.45;
  }
  .contact-name {
    color: var(--accent-blue);
    font-size: 20px;
    font-weight: 600;
    letter-spacing: 0.8px;
    text-transform: uppercase;
    line-height: 1.1;
  }
  .contact-title {
    color: var(--text-white);
    font-size: 12px;
    font-weight: 500;
    margin-bottom: 10px;
  }
  .contact-group { margin-bottom: 10px; }
  .contact-line {
    display: flex;
    align-items: center;
    gap: 5px;
  }
  .contact-line svg { width: 10px; height: 10px; flex: none; }
  .card-back .brand-name {
    position: absolute;
    left: 0;
    right: 0;
    top: 50%;
    transform: translateY(-50%);
    text-align: center;
    font-size: 56px;
  }
</style>
</head>
<body>
<main class="canvas">
  <section class="card card-front" aria-label="Business card front">
    <div class="brand-name">HearthMile</div>
    <div class="divider"></div>
    <div class="contact">
      <div class="contact-name">Marcus Pell</div>
      <div class="contact-title">CEO</div>
      <div class="contact-group">
        <div>NMLS 61947</div>
        <div>Company NMLS 274615</div>
      </div>
      <div class="contact-group">
        <div>48 Birchwell Court,</div>
        <div>Suite 314, Larkmont, NJ 08150</div>
      </div>
      <div class="contact-line">
        <svg viewBox="0 0 10 10" aria-hidden="true"><path d="M2 0.8 L3.6 0.8 L4.3 3 L3.2 3.9 Q4.3 6.1 6.1 6.9 L7 5.8 L9.2 6.5 L9.2 8.1 Q8.5 9.4 7 9.2 Q1.2 8 0.8 2.3 Q0.9 1 2 0.8 Z" fill="var(--accent-blue)"/></svg>
        <span>732-555-0182</span>
      </div>
      <div class="contact-line">
        <svg viewBox="0 0 10 10" aria-hidden="true"><rect x="0.7" y="2" width="8.6" height="6" fill="none" stroke="var(--accent-blue)" stroke-width="1"/><path d="M0.7 2 L5 5.4 L9.3 2" fill="none" stroke="var(--accent-blue)" stroke-width="1"/></svg>
        <span>email@hearthmile.example</span>
      </div>
    </div>
  </section>
  <section class="card card-back" aria-label="Business card back">
    <div class="brand-name">HearthMile</div>
  </section>
</main>
</body>
</html>
```